Modern, clean and professional Wordpress design for a safety training company!

We are currently in the process of creating a new website for our business. We have hired a website developer and the main structure of our new Wordpress site is complete. We now need an overall design plan for the site. We need a very clean, professional and easy to follow website. Most of our website visitors only spend about 30-45 secs on our sites "shopping " so it is imperative that we have a strong Home Page.
Our company specializes in CPR and First Aid Certification Classes to businesses and individuals throughout Northern California. We provide these certifications two ways: ONSITE-We come to you, and HOSTED-we offer weekly classes at our 2 locations.
Our design needs to use the general green and blue colors of our logo. But we also like white.
The final design MUST communicate a legitimate, trustworthy and professional business. Our industry is VERY competitive and we need to STAND OUT.
Currently, the NEW website that we need a new design for is www.LifelineDrillWorks.com
Our old website is www.RescuePrepValleyHub.com and we really do like the design of this website, but we just needed a Wordpress site for SEO purposes.
These are 3 websites that we really:
http://morvaliontech.com/
http://www.tralbex.com/
https://www.plivant.com/
I have attached our Logo and other images if you need to use them but looking at the current two sites will be you best help.
Target Market(s)
1) Large businesses and industries that are looking for a company to provide ONSITE safety training classes at their office or place of work.
2) Individuals that need certifications for their jobs and other needs. These individuals are looking for a legitimate, trustworthy and professional environment to complete their training class.

```html
<!DOCTYPE html>
<html lang="en">
<head>
<meta charset="utf-8">
<title>Crestline Safety Academy</title>
<link href="https://fonts.googleapis.com/css2?family=Roboto:wght@400;500;700&family=Montserrat:wght@600;700&display=swap" rel="stylesheet">
<style>
:root{
  --blue:#3f6bc8;
  --navy:#1b3a8f;
  --green:#8cc21e;
  --green-dark:#6e9e10;
  --text:#333;
  --muted:#555;
  --grey-band:#e9e9e9;
  --footer:#1f1f1f;
}
*{margin:0;padding:0;box-sizing:border-box}
html,body{width:830px;height:1200px;overflow:hidden;background:#fff}
body{position:relative;font-family:"Roboto",sans-serif;color:var(--text)}
.abs{position:absolute}
.brand{left:66px;top:28px;width:140px;text-align:center;color:var(--navy);font-weight:700;font-size:19px;line-height:1.1}
.brand-mark{display:block;width:14px;height:14px;border-radius:50%;background:var(--green);margin:0 auto 6px}
.brand small{display:block;font-size:8px;font-weight:400;letter-spacing:1px;color:var(--green-dark);margin-top:3px}
.contact{right:122px;top:33px;font-size:12px;color:#222;line-height:22px;white-space:nowrap}
.contact div{display:flex;align-items:center;gap:8px}
.contact svg{width:15px;height:15px;flex:none}
.contact .phone{font-size:14px;font-weight:500}
.badge{left:725px;top:19px;width:39px;height:63px;border:2px solid var(--navy);border-radius:3px;background:#fff}
.badge::after{content:"";position:absolute;left:4px;right:4px;bottom:4px;height:10px;background:var(--navy)}
.blue-band{left:0;top:108px;width:830px;height:417px;background:var(--blue)}
.nav{left:63px;top:91px;width:707px;height:46px;background:var(--green);display:flex;font-size:10px;color:#fff;text-transform:uppercase}
.nav a{color:#fff;text-decoration:none;display:flex;align-items:center;justify-content:center;padding:0 20px;flex:auto}
.nav a.active{background:var(--navy);flex:0 0 74px;padding:0}
.hero{left:63px;top:137px;width:707px;height:388px;background:linear-gradient(180deg,#dfe6ea 0%,#b9c2c6 35%,#6f6a6a 70%,#3f3d40 100%)}
.hero-caption{left:63px;top:325px;width:300px;height:91px;background:rgba(60,60,60,.75);color:#fff;padding:16px 0 0 44px}
.hero-caption h2{font-weight:500;font-size:26px}
.hero-caption p{font-size:16px;margin-top:8px}
.dots{left:113px;top:496px;display:flex;gap:6px}
.dots span{width:25px;height:3px;background:#fff}
.dots span:first-child{background:var(--green)}
.welcome{left:60px;top:563px;width:710px;text-align:center}
.welcome h1{font-family:"Montserrat",sans-serif;font-size:16px;font-weight:700;color:#111}
.welcome h1 em{font-style:normal;color:var(--navy)}
.welcome p{font-size:10.5px;line-height:18px;color:var(--muted);margin-top:10px}
.photo{width:215px;height:150px;border:4px solid #fff;box-shadow:0 1px 4px rgba(0,0,0,.4)}
.photo.onsite{left:64px;top:657px;background:linear-gradient(135deg,#3b4150,#7f8a9a 60%,#c9ccd3)}
.photo.hosted{left:308px;top:657px;background:linear-gradient(135deg,#c7cfd8,#7d92b8 55%,#5c6fa8)}
.service{width:215px}
.service h3{font-size:14px;font-weight:400;color:var(--navy)}
.service h3 span{font-size:12px}
.service p{font-size:10px;line-height:15px;color:var(--muted);margin-top:8px;text-align:justify;height:30px;overflow:hidden}
.btn{display:inline-block;margin-top:12px;background:var(--green);color:#fff;font-size:9px;padding:7px 17px;border:1px solid var(--green-dark);border-radius:2px;box-shadow:0 2px 2px rgba(0,0,0,.25)}
.promo{left:553px;width:214px;height:126px;border:4px solid #fff;box-shadow:0 1px 4px rgba(0,0,0,.4);background:linear-gradient(180deg,#c6c8c8,#6b6e70)}
.promo-card{position:absolute;left:37px;top:4px;width:130px;height:110px;background:rgba(255,255,255,.82);text-align:center;padding-top:10px}
.promo-card .price{font-size:16px;color:#222}
.promo-card .who{font-size:12px;color:var(--navy);margin-top:6px;line-height:18px}
.promo-card .reg{display:inline-block;margin-top:6px;background:var(--navy);color:#fff;font-size:8px;padding:5px 8px;border-radius:2px}
.grey-band{left:0;top:937px;width:830px;height:164px;background:var(--grey-band)}
.label{font-size:11px;color:var(--navy)}
.review{left:66px;top:964px;font-size:7.5px;line-height:13px;color:#222}
.review .label{display:block;margin-bottom:10px}
.stars{display:flex;gap:1px;margin-top:4px}
.stars svg{width:19px;height:19px}
.address{left:327px;top:966px;font-size:8.5px;line-height:18px;color:#222}
.address .label{display:block;margin-bottom:6px}
.address .tel{font-size:10px}
.map{left:555px;top:965px;width:216px;height:113px;background:linear-gradient(135deg,#e4e2dc,#d6d3cb)}
.footer{left:0;top:1101px;width:830px;height:99px;background:var(--footer)}
.footer-links{left:63px;top:1134px;font-size:9.5px;color:#ddd}
.copy{left:63px;top:1153px;font-size:11px;color:#ddd}
.social{left:655px;top:1140px;display:flex;gap:7px}
.social span{width:23px;height:23px;border-radius:2px}
</style>
</head>
<body>
<header>
  <div class="abs brand"><span class="brand-mark"></span>Crestline<small>SAFETY ACADEMY</small></div>
  <div class="abs contact">
    <div class="phone"><svg viewBox="0 0 16 16"><circle cx="8" cy="8" r="7" fill="none" stroke="#2a9bd8" stroke-width="1.5"/><path d="M5 4.5l1.5-.5 1 2-1 .8a5 5 0 0 0 2.7 2.7l.8-1 2 1-.5 1.5C9 11.5 4.5 7 5 4.5z" fill="#2a9bd8"/></svg>916-555-0182</div>
    <div><svg viewBox="0 0 16 16"><rect x="1" y="3" width="14" height="10" fill="#2a9bd8"/><path d="M1 3l7 6 7-6" fill="none" stroke="#fff" stroke-width="1.2"/></svg>info@crestlinesafety.com</div>
  </div>
  <div class="abs badge" role="img" aria-label="Accreditation badge"></div>
</header>

<div class="abs blue-band"></div>
<nav class="abs nav">
  <a class="active">Home</a><a>Class Calender</a><a>Classes for Groups</a><a>Certification Classes</a><a>About Us</a><a>Policies</a>
</nav>
<div class="abs hero" role="img" aria-label="Photo of a classroom with students listening to an instructor"></div>
<div class="abs hero-caption"><h2>CPR+First Aid</h2><p>Crestline Safety Academy</p></div>
<div class="abs dots"><span></span><span></span><span></span><span></span><span></span></div>

<section class="abs welcome">
  <h1>WELCOME TO <em>CRESTLINE SAFETY ACADEMY!</em></h1>
  <p>Crestline Safety Academy is Northern California's leader in CPR, BLS, and Basic First Aid Certifications! Taught by experienced Firefighters,<br>our classes are much shorter and provide common sense knowledge and skills to each student to help prepare them for actual emergencies</p>
</section>

<div class="abs photo onsite" role="img" aria-label="Photo of a paramedic performing CPR training"></div>
<div class="abs service" style="left:67px;top:820px">
  <h3>ONSITE <span>- We come to you</span></h3>
  <p>Lorem Ipsum has been the industry's standard dummy text ever since the 1500s, when an</p>
  <span class="btn">READ MORE</span>
</div>
<div class="abs photo hosted" role="img" aria-label="Photo of medical staff practising on a training mannequin"></div>
<div class="abs service" style="left:311px;top:820px">
  <h3>HOSTED <span>- we offer weekly classes</span></h3>
  <p>Lorem Ipsum has been the industry's standard dummy text ever since the 1500s, when an</p>
  <span class="btn">READ MORE</span>
</div>

<div class="abs promo" style="top:659px" role="img" aria-label="Classroom photo behind CPR class offer">
  <div class="promo-card"><div class="price">CPR &nbsp;$39</div><div class="who">Adult/Child/Infant<br>90 Minutes!</div><span class="reg">REGISTER NOW!</span></div>
</div>
<div class="abs promo" style="top:792px" role="img" aria-label="Classroom photo behind BLS class offer">
  <div class="promo-card"><div class="price">BLS &nbsp;$49</div><div class="who">Healthcare/Dental<br>90 Minutes!</div><span class="reg">REGISTER NOW!</span></div>
</div>

<div class="abs grey-band"></div>
<div class="abs review">
  <span class="label">REVIEWS</span>
  Mara L<br>August 11, 2014<br>My husband took the class. I was able to monitor<br>&nbsp;as I had heart surgery...
  <div class="stars">
    <svg viewBox="0 0 20 20"><path d="M10 1l2.7 6 6.3.6-4.8 4.2 1.4 6.4L10 15l-5.6 3.2 1.4-6.4L1 7.6 7.3 7z" fill="#e2b33a" stroke="#9a7a20"/></svg>
    <svg viewBox="0 0 20 20"><path d="M10 1l2.7 6 6.3.6-4.8 4.2 1.4 6.4L10 15l-5.6 3.2 1.4-6.4L1 7.6 7.3 7z" fill="#e2b33a" stroke="#9a7a20"/></svg>
    <svg viewBox="0 0 20 20"><path d="M10 1l2.7 6 6.3.6-4.8 4.2 1.4 6.4L10 15l-5.6 3.2 1.4-6.4L1 7.6 7.3 7z" fill="#e2b33a" stroke="#9a7a20"/></svg>
    <svg viewBox="0 0 20 20"><path d="M10 1l2.7 6 6.3.6-4.8 4.2 1.4 6.4L10 15l-5.6 3.2 1.4-6.4L1 7.6 7.3 7z" fill="#ddd" stroke="#aaa"/></svg>
    <svg viewBox="0 0 20 20"><path d="M10 1l2.7 6 6.3.6-4.8 4.2 1.4 6.4L10 15l-5.6 3.2 1.4-6.4L1 7.6 7.3 7z" fill="#ddd" stroke="#aaa"/></svg>
  </div>
</div>
<div class="abs address">
  <span class="label">ADDRESS</span>
  HARLOWSTRASSE 12 · 40210 VELDEN DE<br>
  <span class="tel">TELEPHONE</span><br>
  + 49 151 000 555 20 ·<br>
  info@samplemail.com
</div>
<div class="abs map" role="img" aria-label="Street map showing the training location"></div>

<footer class="abs footer"></footer>
<div class="abs footer-links">About &nbsp;|&nbsp; Disclaimer &nbsp;|&nbsp; Contact &nbsp;|&nbsp; Sitemap &nbsp;|&nbsp; Special Thanks</div>
<div class="abs copy">Copyright © 2015 &nbsp;All Rights</div>
<div class="abs social">
  <span style="background:#29a9e0" role="img" aria-label="Social link"></span>
  <span style="background:#d02a24" role="img" aria-label="Video channel link"></span>
  <span style="background:#2d4f95" role="img" aria-label="Social link"></span>
  <span style="background:#1577b5" role="img" aria-label="Professional network link"></span>
</div>
</body>
</html>
```